Verpackungen für Shampoos
Zielgruppe
Wir sind ein kleines Familienunternehmen mit 2-3 Friseurfilialen und Onlineshop im Naturfriseurbereich, arbeiten mit ökologischen, nachhaltigen und natürlichen Produkten und vertreiben unsere eigene Haarbürste. Wir betreiben mit Sol Verde unsere eigene Marke in diesem Bereich. Erste Produkte, wie eine eigene Haarbürste sind bereits vorhanden und entstanden.
Für unsere erste Shampoo Serie suchen wir ein klares, cleanes und hochwertiges Design. Die 200ml Shampooflasche kommt komplett in weiß und besteh aus recyceltem Material. Es soll klar die ökologisch nachhaltige und etwas höherpreisige Marke kommuniziert werden. Dabei sehen wir vom Stil „weniger ist mehr“ als ganz klare Designvorgabe. Anbei auch ein Beispiel von Pavura, die das ganze sehr schön umgesetzt haben.
Die INCI sind noch nicht final. Es wäre schön, wenn hier ein Platzhalter eingefügt würde. Da eine der Hauptzielgruppen auch Österreicher sind, würden wir uns über ein kleines „Made in Austria“ auf der Vorderseite (evtl. ganz unten auf der Flasche) freuen.
Insgesamt sind es vier verschiedene Shampoos, die aus der gleichen Serie stammen. Es wäre schön, wenn man diese auch direkt unterscheiden könnte. Vielleicht durch ein grafisches Element, oder einfach nur durch die verschiedenen Namenserweiterungen. Hier die Aufstellung mit den Erweiterungen:
Es werden 4 verschiedene Shampoos, die Namen sind:
Change - Strapaziertes Haar
Lumen - Normales Haar
Sensitiv - Empfindliche Kopfhaut
Balancing - Fettiges Haar
Zielgruppe:
Weiblich, 30-60 Jahre, mittleres bis gehobenes Einkommen, nachhaltig, ökologisch, natürlich, legt Wert auf hochwertige Produkte und Dienstleistungen, achtet auf Konsum.
Aufgabenstellung
Die Landingpage zur Bürste ist hier erreichbar (Beispiel):
Vielleicht hilft das etwas um das Design und die Tonality aufzuschnappen: https://sol-verde.de/gold-birch-wildschweinborstenbuerste/
Es wäre super, wenn das Design der Flasche ähnlich klar und strukturiert ist.
Die Shampoos sind komplett vegan und made in Austria. Die beiden Aspekte sollten in Design auch aufgegriffen werden. Da wir einen 4 farbigen Tamponade/Siebdruck auf der Flasche anwenden, stehen leider nicht so viele Farben zur Verfügung (3-4).
Link zur Flasche:
https://www.brumoxa.com/de/kosmetik/varleno/varleno-tubica/flasche-heavy-200ml-24-410-plastik
Des Weiteren kann sich noch am Sol Verde Haarkonzept und unserem Dienstleistungsflyer orientiert werden.
Benefits:
-       Pflegt das Haar, hält es geschmeidig
- Bio Shampoo Konzentrat
-       Die Grundlage für gesunde Kopfhaut und schönes Haar*
-       Vermindert Spliss*
-       Hält die Haare natürlich geschmeidig
-       Regt die Durchblutung der Kopfhaut an
-       Verteilt Nährstoffe von der Wurzel bis in die Spitzen*
-       Verbessert das Kopfhautklima*
-       Für eine gut durchblutete und gesunde Kopfhaut mit glänzenden und
geschmeidigen Haaren*
-       Entfernt Schuppen und abgestorbene Hautpartikel
-       Verbessert natürlich die allgemeine Haarstruktur
-       Entwirrt langes und gelocktes Haar
-       Reinigt die Kopfhaut ohne Chemie*
-       Mehr Volumen im Haar
-       Mehr Stand im Haar durch Kräftigung der Haarbalkmuskulatur
-       Spart Shampoo und hilft Shampoo seltener und weniger zu nutzen
-       Nährstoffversorgung bis in die Haarspitzen
Inhaltsstoffe:
Lumen
Aloe Vera Direktsaft*, Decyl Glucoside, Coco Glucoside, Lauryl Glucoside, Hopfenextrakt*, Pentylene Glycol green, Meli..

```html
<!DOCTYPE html>
<html lang="de">
<head>
<meta charset="utf-8">
<title>Lumen – Shampoo für normales Haar</title>
<link rel="stylesheet" href="https://fonts.googleapis.com/css2?family=Playfair+Display:wght@400&family=Sacramento&family=Roboto+Condensed:wght@700&display=swap">
<style>
  :root {
    --paper: #ffffff;
    --sage: #c5dbb1;
    --accent-orange: #f4aa1b;
    --ink-grey: #7b7b7b;
    --badge-grey: #8a8a8a;
  }
  html, body {
    margin: 0;
    padding: 0;
    overflow: hidden;
    background: var(--paper);
  }
  .label {
    position: relative;
    width: 848px;
    height: 1200px;
    background: var(--paper);
    overflow: hidden;
  }
  .color-code {
    position: absolute;
    left: 340px;
    top: 363px;
    width: 69px;
    height: 124px;
    background: var(--accent-orange);
  }
  .variant-dot {
    position: absolute;
    left: 373px;
    top: 543px;
    width: 96px;
    height: 96px;
    border-radius: 50%;
    background: var(--sage);
  }
  .variant-name {
    position: absolute;
    left: 0;
    width: 848px;
    top: 656px;
    margin: 0;
    text-align: center;
    font-family: "Sacramento", cursive;
    font-weight: 400;
    font-size: 44px;
    color: var(--sage);
    line-height: 1;
  }
  .divider-dot {
    position: absolute;
    left: 421px;
    top: 710px;
    width: 6px;
    height: 6px;
    border-radius: 50%;
    background: var(--sage);
  }
  .variant-description {
    position: absolute;
    left: 0;
    width: 848px;
    top: 727px;
    margin: 0;
    text-align: center;
    font-family: "Playfair Display", serif;
    font-weight: 400;
    font-size: 13.5px;
    line-height: 17px;
    color: var(--ink-grey);
  }
  .origin-badges {
    position: absolute;
    top: 888px;
    left: 374px;
    width: 96px;
    height: 50px;
    display: flex;
    font-family: "Roboto Condensed", sans-serif;
    font-weight: 700;
    font-size: 7px;
    line-height: 7.5px;
    color: var(--badge-grey);
  }
  .badge {
    flex: 1;
    display: flex;
    flex-direction: column;
    align-items: center;
    padding-top: 8px;
    text-align: center;
  }
  .badge svg { margin-bottom: 3px; }
  .badge-separator {
    width: 1px;
    height: 48px;
    background: var(--badge-grey);
  }
</style>
</head>
<body>
  <main class="label">
    <div class="color-code" role="img" aria-label="Orangefarbener Pinselstrich als Farbkennung der Sorte"></div>

    <div class="variant-dot"></div>
    <h1 class="variant-name">Lumen</h1>
    <div class="divider-dot"></div>
    <p class="variant-description">Shampoo für<br>normales Haar</p>

    <div class="origin-badges">
      <div class="badge">
        <svg width="12" height="8" viewBox="0 0 12 8" aria-hidden="true">
          <rect x="0" y="0" width="12" height="2" rx="1" fill="var(--badge-grey)"/>
          <rect x="0" y="5.5" width="12" height="2" rx="1" fill="var(--badge-grey)"/>
        </svg>
        <span>Made in<br>AUSTRIA</span>
      </div>
      <div class="badge-separator"></div>
      <div class="badge">
        <svg width="12" height="11" viewBox="0 0 12 11" aria-hidden="true">
          <path d="M1 1 L4.5 10 L7 4" fill="none" stroke="var(--badge-grey)" stroke-width="1.2"/>
          <path d="M5.5 6 Q6 1 11.5 0 Q11 5 5.5 6 Z" fill="var(--badge-grey)"/>
        </svg>
        <span>100 %<br>VEGAN</span>
      </div>
    </div>
  </main>
</body>
</html>
```